Brand new redesign of Brightpath finance website

I need a new website design that i can advertise a great low interest rate on the front page and capture input application details that will send through to my email address.

some car finance companies will be similar to this would be listed below

tallowcredit.example.com.au
mirabelfinance.example.com.au
finance725.example.com.au
quenbyfinance.example.com.au
finance91.example.com.au

Reason: I have changed the project to a committed project. all the webpages should have the same format just different content and i want to be able to edit the front page easily to update my interest rates.

Target Market(s)

Australian Finance market targeting a younger demographic

Industry/Entity Type

Finance

Coding

Coded - Design and coding required

Number of Pages Required

5+ page

Font styles to use
Serif
Sans Serif

Colors
0255a3
ffffff
cedeed

Requirements
Must have
• application capture form
• apply now buttons
• Headline rate front page

```html
<!DOCTYPE html>
<html lang="en">
<head>
<meta charset="utf-8">
<title>Brightpath finance</title>
<link rel="stylesheet" href="https://fonts.googleapis.com/css2?family=Lato:ital,wght@0,400;0,700;0,900;1,400&family=Questrial&display=swap">
<style>
:root{
  --brand:#0255a3;
  --brand-dark:#033f7a;
  --ice:#cedeed;
  --white:#ffffff;
  --ink:#222831;
  --muted:#555c66;
  --paper:#f1f1f1;
  --night:#1f1f1f;
  --photo-warm:#8a7565;
  --photo-dark:#2f3236;
}
*{box-sizing:border-box;margin:0;padding:0}
html,body{width:1200px;height:2228px;overflow:hidden}
body{position:relative;font-family:"Lato",sans-serif;color:var(--ink);background:var(--white)}
.abs{position:absolute}

/* header */
.site-header{left:0;top:0;width:1200px;height:88px;background:var(--white);border-top:3px solid #ddd}
.brand{left:162px;top:22px;display:flex;align-items:center;gap:12px}
.brand-dot{width:44px;height:44px;border-radius:50%;background:var(--brand)}
.brand-name{font-family:"Questrial",sans-serif;font-size:30px;color:var(--brand);letter-spacing:1px}
.apply-btn{left:745px;top:31px;width:116px;height:31px;background:var(--brand);color:var(--white);font-size:11px;font-weight:900;letter-spacing:.5px;display:flex;align-items:center;justify-content:center}
.header-phone{left:890px;top:32px;display:flex;align-items:center;gap:10px;font-size:20px;color:var(--brand)}

/* nav */
.main-nav{left:0;top:88px;width:1200px;height:46px;background:var(--brand)}
.nav-item{top:0;height:46px;line-height:46px;font-size:14px;color:var(--white);text-transform:uppercase;transform:translateX(-50%)}
.nav-item.is-active{background:var(--ice);color:var(--brand-dark);width:94px;text-align:center}

/* hero */
.hero-photo{left:0;top:134px;width:741px;height:509px;background:linear-gradient(120deg,#3a3c40 0%,#6d6764 35%,#b39c8e 55%,#7b746f 80%,#c9c9c7 100%)}
.hero-side{left:1039px;top:134px;width:161px;height:509px;background:linear-gradient(180deg,#8c9297,#d8d8d6)}
.badge-shape{left:160px;top:443px;width:184px;height:184px;border-radius:50%;border:6px solid rgba(255,255,255,.85);background:rgba(255,255,255,.08)}
.rate-list{left:374px;top:462px;width:338px}
.rate-item{display:flex;align-items:flex-start;gap:8px;background:rgba(206,222,237,.92);margin-bottom:4px;padding:6px 10px;font-size:15px;color:#1c2430;line-height:26px}
.rate-item svg{flex:none;margin-top:5px}

.quote-panel{left:741px;top:134px;width:298px;height:509px;background:var(--ice)}
.quote-title{left:16px;top:38px;width:266px;height:36px;background:var(--brand);color:var(--white);font-size:17px;display:flex;align-items:center;justify-content:center;letter-spacing:.3px}
.field{left:16px;width:266px;height:37px;background:var(--white);font-size:12px;font-style:italic;color:#555;padding:0 8px;display:flex;align-items:center}
.agree{left:16px;top:382px;font-size:13px;color:#333;display:flex;align-items:center;gap:7px}
.agree .box{width:9px;height:9px;border:1px solid #888;background:var(--white)}
.agree a{color:var(--brand);text-decoration:none}
.quote-submit{left:24px;top:419px;width:252px;height:49px;background:var(--brand);color:var(--white);font-weight:700;font-size:16px;display:flex;align-items:center;justify-content:center;box-shadow:0 2px 0 var(--brand-dark)}

/* pre approval */
.preapproval{left:0;top:643px;width:1200px;height:304px;background:var(--paper)}
.section-title{left:0;width:1200px;text-align:center;font-family:"Questrial",sans-serif;font-size:29px;font-weight:700}
.divider{left:368px;width:464px;height:1px;background:#c9c9c9}
.divider-dot{left:586px;width:28px;height:28px;border-radius:50%;background:var(--brand);border:3px solid var(--ice)}
.intro{left:0;top:138px;width:1200px;text-align:center;font-size:16px;line-height:30px;color:#333}
.intro strong{color:#111}

/* loans */
.loans{left:0;top:947px;width:1200px;height:546px;background:linear-gradient(90deg,#2a2d31 0%,#3c3a38 45%,#5a4a40 70%,#3a3431 100%)}
.loans .section-title{color:var(--white)}
.loan-card{top:152px;width:205px;height:313px;background:var(--white)}
.loan-img{left:15px;top:15px;width:175px;height:123px}
.loan-name{left:0;top:155px;width:205px;text-align:center;font-family:"Questrial",sans-serif;font-weight:700;font-size:21px;color:var(--brand)}
.loan-text{left:20px;top:194px;width:165px;text-align:center;font-size:11.5px;line-height:18px;color:#333}
.read-more{left:39px;top:265px;width:116px;height:30px;border:1px solid var(--brand);color:var(--brand);font-size:11px;font-weight:700;display:flex;align-items:center;justify-content:center}

/* calculator */
.repay{left:0;top:1493px;width:1200px;height:191px;background:var(--white)}
.repay-title{left:162px;top:50px;font-size:42px;font-weight:700;color:var(--brand)}
.repay-sub{left:163px;top:110px;font-size:18px;font-weight:700;color:#333}
.calc-btn{left:806px;top:63px;width:196px;height:51px;background:var(--brand);color:var(--white);font-weight:700;font-size:16px;letter-spacing:.5px;display:flex;align-items:center;justify-content:center;box-shadow:0 2px 0 var(--brand-dark)}

/* guaranteed */
.guarantee{left:0;top:1684px;width:1200px;height:188px;background:linear-gradient(90deg,#6b4a36 0%,#3b3432 20%,#2a2c30 60%,#4a4038 100%)}
.guarantee-title{left:163px;top:52px;font-size:27px;color:var(--white)}
.guarantee-sub{left:163px;top:108px;font-size:18px;font-weight:700;color:var(--white)}
.more-btn{left:806px;top:68px;width:196px;height:52px;background:var(--ice);color:var(--brand);font-weight:700;font-size:16px;letter-spacing:.5px;display:flex;align-items:center;justify-content:center;border-left:3px solid var(--brand);border-right:3px solid var(--brand)}

/* footer */
.site-footer{left:0;top:1872px;width:1200px;height:311px;background:var(--brand);color:var(--white)}
.foot-head{top:26px;font-family:"Questrial",sans-serif;font-size:19px;letter-spacing:1px;padding-bottom:8px;border-bottom:1px solid rgba(255,255,255,.25)}
.foot-links{left:162px;top:68px;list-style:none;font-size:14px;line-height:30.5px}
.foot-links li::before{content:"";display:inline-block;border-left:5px solid var(--white);border-top:4px solid transparent;border-bottom:4px solid transparent;margin-right:10px}
.foot-links li.is-current{color:var(--ice);opacity:.8}
.contact-row{left:375px;display:flex;gap:16px;font-size:14px;line-height:20px}
.contact-row svg{flex:none;margin-top:2px}
.social-row{left:672px;display:flex;align-items:center;gap:14px;font-size:14px}
.social-square{width:24px;height:24px;background:rgba(255,255,255,.25)}
.copyright{left:0;top:2183px;width:1200px;height:45px;background:var(--night);color:var(--white);font-size:12.5px;display:flex;align-items:center;justify-content:center}
</style>
</head>
<body>

<header class="site-header abs">
  <div class="brand abs"><span class="brand-dot"></span><span class="brand-name">BRIGHTPATH FINANCE</span></div>
  <div class="apply-btn abs">APPLY NOW</div>
  <div class="header-phone abs">
    <svg width="20" height="20" viewBox="0 0 24 24"><path fill="#222" d="M6.6 10.8a15 15 0 006.6 6.6l2.2-2.2a1 1 0 011-.25 11.4 11.4 0 003.6.6 1 1 0 011 1V20a1 1 0 01-1 1A17 17 0 013 4a1 1 0 011-1h3.5a1 1 0 011 1 11.4 11.4 0 00.6 3.6 1 1 0 01-.25 1z"/></svg>
    <span>123-456-7890</span>
  </div>
</header>

<nav class="main-nav abs">
  <div class="nav-item abs is-active" style="left:208px">Home</div>
  <div class="nav-item abs" style="left:316px">About Us</div>
  <div class="nav-item abs" style="left:434px">Vehicle Loans</div>
  <div class="nav-item abs" style="left:565px">Other Loans</div>
  <div class="nav-item abs" style="left:682px">Insurance</div>
  <div class="nav-item abs" style="left:829px">Finance Calculator</div>
  <div class="nav-item abs" style="left:982px">Contact Us</div>
</nav>

<section class="hero">
  <div class="hero-photo abs" role="img" aria-label="Photo of a smiling young woman in a car holding keys"></div>
  <div class="hero-side abs" role="img" aria-label="Photo of a car interior and door"></div>
  <div class="badge-shape abs" role="img" aria-label="Low rate guarantee badge"></div>
  <div class="rate-list abs">
    <div class="rate-item"><svg width="16" height="14" viewBox="0 0 16 14"><path d="M1 7l5 5L15 1" fill="none" stroke="#111" stroke-width="3"/></svg><span>LOW RATE CAR LOANS FROM 4.69%<br>COMPARISON RATE 4.99%*</span></div>
    <div class="rate-item"><svg width="16" height="14" viewBox="0 0 16 14"><path d="M1 7l5 5L15 1" fill="none" stroke="#111" stroke-width="3"/></svg><span>LOW FEES</span></div>
    <div class="rate-item"><svg width="16" height="14" viewBox="0 0 16 14"><path d="M1 7l5 5L15 1" fill="none" stroke="#111" stroke-width="3"/></svg><span>LOW TOTAL COST LOANS</span></div>
  </div>

  <form class="quote-panel abs">
    <div class="quote-title abs">QUICK &amp; EASY QUOTE</div>
    <div class="field abs" style="top:94px">First Name*</div>
    <div class="field abs" style="top:151px">Last Name*</div>
    <div class="field abs" style="top:209px">Email Address*</div>
    <div class="field abs" style="top:267px">Phone Number*</div>
    <div class="field abs" style="top:324px">Loan Amount in dollars *</div>
    <div class="agree abs"><span class="box"></span><span>I agree to the <a>Terms &amp; Conditions</a></span></div>
    <div class="quote-submit abs">GET MY BEST RATE NOW</div>
  </form>
</section>

<section class="preapproval abs">
  <h2 class="section-title abs" style="top:38px">Online Loan Pre Approval</h2>
  <div class="divider abs" style="top:99px"></div>
  <div class="divider-dot abs" style="top:85px"></div>
  <p class="intro abs">Complete our short online application to get finance for your car, truck, motorbike, equipment, boat or caravan!<br>We have helped thousands of Australians obtain the finance they need to buy a new or used vehicle.<br><strong>We'll find you competitive vehicle finance that'll get you on the road fast and if you've had credit issues in the past,<br>we also have access to specialist lenders who could help.</strong></p>
</section>

<section class="loans abs" role="img" aria-label="Background photo of a family in front of a house">
  <h2 class="section-title abs" style="top:34px">We Offer Loans For</h2>
  <div class="divider abs" style="top:97px;background:rgba(255,255,255,.4)"></div>
  <div class="divider-dot abs" style="top:83px"></div>

  <div class="loan-card abs" style="left:162px">
    <div class="loan-img abs" role="img" aria-label="Photo of a car sale handshake" style="background:linear-gradient(135deg,#c9ced4,#8a8f96)"></div>
    <h3 class="loan-name abs">Vehicle Loans</h3>
    <p class="loan-text abs">Lorem ipsum dolor sit amet, consectetur adipiscing elit. Integer vitae interdum mi</p>
    <div class="read-more abs">Read More</div>
  </div>
  <div class="loan-card abs" style="left:386px">
    <div class="loan-img abs" role="img" aria-label="Photo of a white motor yacht at sea" style="background:linear-gradient(180deg,#2f6fb8,#1b4f8a)"></div>
    <h3 class="loan-name abs">Boat Loans</h3>
    <p class="loan-text abs">Lorem ipsum dolor sit amet, consectetur adipiscing elit. Integer vitae interdum mi</p>
    <div class="read-more abs">Read More</div>
  </div>
  <div class="loan-card abs" style="left:610px">
    <div class="loan-img abs" role="img" aria-label="Photo of a model house on building plans" style="background:linear-gradient(135deg,#c9a27a,#8d6a4c)"></div>
    <h3 class="loan-name abs">Home Loans</h3>
    <p class="loan-text abs">Lorem ipsum dolor sit amet, consectetur adipiscing elit. Integer vitae interdum mi</p>
    <div class="read-more abs">Read More</div>
  </div>
  <div class="loan-card abs" style="left:834px">
    <div class="loan-img abs" role="img" aria-label="Photo of a couple meeting an adviser" style="background:linear-gradient(135deg,#d9dbdd,#7d6a5f)"></div>
    <h3 class="loan-name abs">Personal Loans</h3>
    <p class="loan-text abs">Lorem ipsum dolor sit amet, consectetur adipiscing elit. Integer vitae interdum mi</p>
    <div class="read-more abs">Read More</div>
  </div>
</section>

<section class="repay abs">
  <h2 class="repay-title abs">What will my repayments be?</h2>
  <p class="repay-sub abs">See how much you could borrow with our loan calculator.</p>
  <div class="calc-btn abs">LOAN CALCULATOR</div>
</section>

<section class="guarantee abs" role="img" aria-label="Background photo of a model house on stacked coins">
  <h2 class="guarantee-title abs">Find out what Guaranteed Approval actually means</h2>
  <p class="guarantee-sub abs">We explain what it means and what we offer instead.</p>
  <div class="more-btn abs">FIND OUT MORE</div>
</section>

<footer class="site-footer abs">
  <h4 class="foot-head abs" style="left:162px;width:147px">QUICK LINKS</h4>
  <ul class="foot-links abs">
    <li class="is-current">Home</li>
    <li>About Us</li>
    <li>Vehicle Loans</li>
    <li>Other Loans</li>
    <li>Insurance</li>
    <li>Finance Calculator</li>
    <li>Contact us</li>
  </ul>

  <h4 class="foot-head abs" style="left:377px;width:225px">CONTACT&nbsp; DETAILS</h4>
  <div class="contact-row abs" style="top:78px">
    <svg width="14" height="20" viewBox="0 0 14 20"><path fill="#fff" d="M7 0a7 7 0 00-7 7c0 5 7 13 7 13s7-8 7-13a7 7 0 00-7-7zm0 9.5A2.5 2.5 0 117 4.5a2.5 2.5 0 010 5z"/></svg>
    <span>Company Name<br>Street Name, City Name<br>State Name - 123456</span>
  </div>
  <div class="contact-row abs" style="top:167px">
    <svg width="16" height="16" viewBox="0 0 24 24"><path fill="#fff" d="M6.6 10.8a15 15 0 006.6 6.6l2.2-2.2a1 1 0 011-.25 11.4 11.4 0 003.6.6 1 1 0 011 1V20a1 1 0 01-1 1A17 17 0 013 4a1 1 0 011-1h3.5a1 1 0 011 1 11.4 11.4 0 00.6 3.6 1 1 0 01-.25 1z"/></svg>
    <span>123-456-7890</span>
  </div>
  <div class="contact-row abs" style="top:210px">
    <svg width="18" height="16" viewBox="0 0 18 16"><rect x="4" y="0" width="10" height="4" fill="#fff"/><rect x="0" y="5" width="18" height="7" rx="1" fill="#fff"/><rect x="4" y="10" width="10" height="6" fill="#fff" stroke="#0255a3" stroke-width="1"/></svg>
    <span>123-456-7890</span>
  </div>
  <div class="contact-row abs" style="top:252px">
    <svg width="14" height="12" viewBox="0 0 14 12"><rect width="14" height="12" fill="#fff"/><path d="M0 0l7 6 7-6" fill="none" stroke="#0255a3" stroke-width="1.3"/></svg>
    <span>info@brightpathfinance.example.com</span>
  </div>

  <h4 class="foot-head abs" style="left:672px;width:127px">FOLLOW&nbsp; US</h4>
  <div class="social-row abs" style="top:80px"><span class="social-square"></span>Friendwall</div>
  <div class="social-row abs" style="top:128px"><span class="social-square"></span>Chirpline</div>
  <div class="social-row abs" style="top:176px"><span class="social-square"></span>Worknet</div>
  <div class="social-row abs" style="top:224px"><span class="social-square"></span>Circlespace</div>
</footer>

<div class="copyright abs">Copyright © 2016&nbsp; Brightpath finance. All Right Reserved</div>

</body>
</html>
```